Foot doctor needs feet friendly business cards.

Business cards for Podiatrist. Needs to look professional and modern. Back side put an appointment card, and try to put a little basic street map somewhere on card along with all of our contact info below:

Marcus Dovan, DPM, Inc.
Diplomate, National Council of Lower Limb Medicine
Call: 1.877.Toes.482
1.555.283.9146
Fax: 1.555.671.3820
Email: info@DrDovanclinic.example
Web: www.DrDovanclinic.example
2847 W. Harbor Ln. Suite 204
Bayside Vale, CA 90000

```html
<!DOCTYPE html>
<html lang="en">
<head>
<meta charset="utf-8">
<title>Marcus Dovan, DPM – Business &amp; Appointment Card</title>
<link href="https://fonts.googleapis.com/css2?family=Source+Sans+3:ital,wght@0,400;0,600;1,400;1,600&display=swap" rel="stylesheet">
<style>
  :root{
    --stage:#000000;
    --card:#ffffff;
    --navy:#1f4b85;
    --ink:#111111;
    --rule:#8fa6c8;
    --skin-light:#f3dccb;
    --skin-mid:#e2b89b;
    --skin-deep:#cf9a7c;
  }
  html,body{margin:0;padding:0;width:1200px;height:900px;overflow:hidden;background:var(--stage);}
  body{position:relative;font-family:"Source Sans 3",sans-serif;}
  .card{position:absolute;top:275px;width:477px;height:294px;background:var(--card);overflow:hidden;}
  .card--front{left:116px;border-radius:0 52px 0 52px;}
  .card--back{left:622px;top:276px;height:293px;border-radius:52px 0 52px 0;}

  .feet-photo{position:absolute;left:0;top:62px;width:310px;height:232px;
    background:
      radial-gradient(ellipse at 45% 60%, var(--skin-mid) 0%, var(--skin-light) 50%, rgba(255,255,255,0) 78%),
      linear-gradient(90deg, var(--skin-deep) 0%, var(--skin-mid) 40%, rgba(255,255,255,0) 100%);
    -webkit-mask-image:linear-gradient(180deg, transparent 0%, #000 22%);
    mask-image:linear-gradient(180deg, transparent 0%, #000 22%);
    opacity:.9;}

  .front-name{position:absolute;right:21px;top:24px;margin:0;color:var(--navy);font-size:21px;font-weight:600;white-space:nowrap;}
  .front-title{position:absolute;right:21px;top:57px;margin:0;color:var(--ink);font-size:13.5px;white-space:nowrap;}
  .front-address{position:absolute;right:21px;top:100px;margin:0;color:var(--ink);font-size:14.5px;line-height:20px;text-align:right;font-style:normal;}
  .contact-list{position:absolute;right:21px;top:170px;margin:0;padding:0;list-style:none;}
  .contact-list li{display:flex;justify-content:flex-end;align-items:center;height:20px;color:var(--ink);font-size:14.5px;white-space:nowrap;}
  .contact-list .icon{width:12px;height:12px;margin-left:9px;flex:none;}
  .contact-list .icon--blank{visibility:hidden;}

  .appt-heading{position:absolute;left:0;right:0;top:34px;margin:0;text-align:center;color:var(--navy);font-size:15.5px;font-weight:600;font-style:italic;letter-spacing:.3px;}
  .appt-field{position:absolute;left:57px;width:365px;height:18px;border-bottom:1px solid var(--rule);color:var(--navy);font-size:13.5px;line-height:16px;}
  .appt-field span.time{position:absolute;left:170px;}
  .appt-note{position:absolute;left:0;width:460px;top:192px;margin:0;text-align:center;color:var(--navy);font-size:14px;font-style:italic;line-height:21px;}
  .appt-web{position:absolute;left:0;width:460px;top:240px;margin:0;text-align:center;color:var(--navy);font-size:14px;}
</style>
</head>
<body>

<section class="card card--front" aria-label="Business card front">
  <div class="feet-photo" role="img" aria-label="Photo of several bare feet with soles and toes toward the viewer"></div>
  <h1 class="front-name">Marcus Dovan, DPM, Inc.</h1>
  <p class="front-title">Diplomate, National Council of Lower Limb Medicine</p>
  <address class="front-address">2847 W. Harbor Ln. Suite 204<br>Bayside Vale, CA 90000</address>
  <ul class="contact-list">
    <li>1.877.Toes.482
      <svg class="icon" viewBox="0 0 12 12" aria-hidden="true"><path d="M1 4c0-1.5 2-2.5 5-2.5S11 2.5 11 4v1H8.5V3.8h-5V5H1z M3 6h6l1.5 4.5h-9z" fill="#2a5b9a"/></svg></li>
    <li>1.555.283.9146
      <svg class="icon icon--blank" viewBox="0 0 12 12" aria-hidden="true"></svg></li>
    <li>1.555.671.3820
      <svg class="icon" viewBox="0 0 12 12" aria-hidden="true"><rect x="1.5" y="4" width="9" height="7" rx="1" fill="#2a5b9a"/><rect x="3.5" y="1" width="5" height="4" fill="#2a5b9a"/><rect x="4" y="6" width="4" height="1" fill="#fff"/><rect x="4" y="8" width="4" height="1" fill="#fff"/></svg></li>
    <li>info@DrDovanclinic.example
      <svg class="icon" viewBox="0 0 12 12" aria-hidden="true"><rect x="1" y="2.5" width="10" height="7" fill="#2a5b9a"/><path d="M1 2.5l5 4 5-4" fill="none" stroke="#fff" stroke-width="1"/></svg></li>
    <li>www.DrDovanclinic.example
      <svg class="icon" viewBox="0 0 12 12" aria-hidden="true"><g fill="none" stroke="#2a5b9a" stroke-width="1.5"><rect x="1.2" y="5.2" width="6" height="3.4" rx="1.7" transform="rotate(-45 4.2 6.9)"/><rect x="4.8" y="3.4" width="6" height="3.4" rx="1.7" transform="rotate(-45 7.8 5.1)"/></g></svg></li>
  </ul>
</section>

<section class="card card--back" aria-label="Appointment card back">
  <h2 class="appt-heading">APPOINTMENT</h2>
  <div class="appt-field" style="top:68px;">For :</div>
  <div class="appt-field" style="top:100px;">Date :<span class="time">Time :</span></div>
  <div class="appt-field" style="top:132px;">Location :</div>
  <div class="appt-field" style="top:161px;"></div>
  <p class="appt-note">If you&nbsp; are unable to keep appointment, please contact<br>us as soon as possible. Call&nbsp; 877 555 0192</p>
  <p class="appt-web">www.DrDovanclinic.example</p>
</section>

</body>
</html>
```